TALMORK

The business want a professional looking business card. We have a scetch we will add but want the extra upgrade, and would like more suggestions for variations of our business cards.

```html
<!DOCTYPE html>
<html lang="en">
<head>
<meta charset="UTF-8">
<title>TALMORK Business Card</title>
<link href="https://fonts.googleapis.com/css2?family=Cinzel:wght@500;600&family=Manrope:wght@400;500&display=swap" rel="stylesheet">
<style>
  :root {
    --bg: #d8d8d6;
    --gold-light: #ece5cf;
    --gold-soft: #d9c692;
    --gold-mid: #b99c5f;
    --gold-deep: #7c6131;
    --ink: #6a4c21;
    --ink-soft: #7a5c2e;
    --faint: rgba(255, 255, 255, 0.28);
  }
  * { margin: 0; padding: 0; box-sizing: border-box; }
  html, body {
    width: 1125px;
    height: 1200px;
    overflow: hidden;
    background: var(--bg);
  }
  .canvas {
    position: relative;
    width: 1125px;
    height: 1200px;
  }
  .card {
    position: absolute;
    left: 150px;
    width: 825px;
    height: 472px;
    border-radius: 22px;
    overflow: hidden;
    background: linear-gradient(90deg,
      var(--gold-soft) 0%,
      var(--gold-light) 9%,
      var(--gold-soft) 30%,
      var(--gold-mid) 58%,
      var(--gold-deep) 100%);
    box-shadow: 0 6px 10px rgba(0, 0, 0, 0.22);
  }
  .card--front { top: 98px; }
  .card--back { top: 631px; }

  /* Front */
  .holder {
    position: absolute;
    left: 129px;
    top: 80px;
    color: var(--ink);
  }
  .holder__company {
    font-family: "Cinzel", serif;
    font-weight: 600;
    font-size: 38px;
    letter-spacing: 0.5px;
    line-height: 1;
  }
  .holder__role {
    margin-top: 14px;
    font-family: "Manrope", sans-serif;
    font-weight: 500;
    font-size: 32px;
    line-height: 1.1;
  }
  .holder__name {
    margin-top: 4px;
    font-family: "Manrope", sans-serif;
    font-weight: 400;
    font-size: 19px;
    color: var(--ink-soft);
  }
  .contact {
    position: absolute;
    left: 129px;
    top: 284px;
    list-style: none;
    font-family: "Manrope", sans-serif;
    font-size: 24px;
    color: var(--ink);
  }
  .contact__item {
    display: flex;
    align-items: center;
    height: 32px;
    margin-bottom: 9px;
  }
  .contact__icon {
    width: 22px;
    height: 22px;
    margin-right: 14px;
    fill: var(--ink);
  }
  .front-mark {
    position: absolute;
    left: 500px;
    top: 165px;
    width: 220px;
    text-align: center;
    color: var(--ink-soft);
  }
  .front-mark__dot {
    display: block;
    width: 56px;
    height: 56px;
    margin: 0 auto 22px;
    border-radius: 50%;
    background: var(--gold-soft);
    opacity: 0.8;
  }
  .front-mark__name {
    font-family: "Cinzel", serif;
    font-weight: 500;
    font-size: 22px;
    letter-spacing: 6px;
    color: var(--ink-soft);
  }
  .front-mark__since {
    margin-top: 2px;
    font-family: "Manrope", sans-serif;
    font-size: 9px;
    letter-spacing: 3px;
    color: var(--ink-soft);
  }

  /* Back */
  .back-motif {
    position: absolute;
    left: 10px;
    top: 15px;
    width: 380px;
    height: 380px;
    border-radius: 50%;
    background: var(--faint);
  }
  .back-brand {
    position: absolute;
    left: 340px;
    top: 300px;
    width: 440px;
    text-align: center;
    color: var(--ink);
  }
  .back-brand__name {
    font-family: "Cinzel", serif;
    font-weight: 500;
    font-size: 56px;
    letter-spacing: 14px;
    line-height: 1;
  }
  .back-brand__since {
    margin-top: 14px;
    font-family: "Manrope", sans-serif;
    font-weight: 500;
    font-size: 20px;
    letter-spacing: 7px;
  }
</style>
</head>
<body>
<main class="canvas">
  <section class="card card--front">
    <div class="holder">
      <h1 class="holder__company">TALMORK LAUVSTAD</h1>
      <p class="holder__role">CEO &amp; Founder</p>
      <p class="holder__name">Henrik Aas Lauvstad</p>
    </div>

    <ul class="contact">
      <li class="contact__item">
        <svg class="contact__icon" viewBox="0 0 24 24" aria-hidden="true">
          <path d="M3 8c0-2 3-4 9-4s9 2 9 4v2h-5V8H8v2H3z"/>
          <path d="M6 11h12l2 9H4z"/>
        </svg>
        <span>004795550142</span>
      </li>
      <li class="contact__item">
        <svg class="contact__icon" viewBox="0 0 24 24" aria-hidden="true">
          <path d="M2 9l10-7 10 7v12H2z M4 10v9h16v-9l-8 6z"/>
        </svg>
        <span>post@talmork.llc</span>
      </li>
      <li class="contact__item">
        <svg class="contact__icon" viewBox="0 0 24 24" aria-hidden="true">
          <path d="M12 2a10 10 0 1 0 0 20a10 10 0 1 0 0-20z M8 6c2 1 3 3 2 5s-3 2-3 5l-2 1A8 8 0 0 1 8 6z M14 13c2 0 3 2 2 4l-2 2c-1-2-2-4 0-6z"/>
        </svg>
        <span>www.talmork.llc</span>
      </li>
    </ul>

    <div class="front-mark">
      <span class="front-mark__dot"></span>
      <p class="front-mark__name">TALMORK</p>
      <p class="front-mark__since">SINCE 2026</p>
    </div>
  </section>

  <section class="card card--back">
    <div class="back-motif"></div>
    <div class="back-brand">
      <p class="back-brand__name">TALMORK</p>
      <p class="back-brand__since">SINCE 2026</p>
    </div>
  </section>
</main>
</body>
</html>
```